Lumora Systems New Website - IT Infrastructure | Smart Cabinet | Micro Data Center

We're an IT SI providing Server Room Design & Build | All-in-One Rack & Smart Cabinet | Structured Cabling | IT Relocation | Maintenance. Old website can be found at www.lumorasys.com.hk. We'd like a brand new wix website which is modern, minimalist, interactive with some animation. Website content will be mostly static and include our service, our project, news and events, about us, contacts, blogs, partners and brands, etc.

reference sites:
We'd like to see more designs referring to below

https://www.pixelvane.example/design/41736205
https://www.pixelvane.example/design/41892417
https://velbrinn.example/

Animation (scrolling effect) referring to
https://velbrinn.example/intelligence/smart-office-room/
Updates

we'd like below style.

Designs look the same

Target Market(s)

Commercials in HK

Industry/Entity Type

IT, Technology, Data Center

Coding

Coded - Design and coding required

Font styles to use
Sans Serif

Requirements
Must have
• CMS, Some Interactive Elements/ Graphics

```html
<!DOCTYPE html>
<html lang="en">
<head>
<meta charset="utf-8">
<title>Lumora Systems — IT Infrastructure</title>
<link rel="stylesheet" href="https://fonts.googleapis.com/css2?family=Ubuntu:wght@400;500;700&family=Josefin+Sans:wght@400;600;700&display=swap">
<style>
:root{
  --dark:#2b2b2b;
  --darker:#1c1c1c;
  --red:#d8392a;
  --red-deep:#b72a1d;
  --card:#2c3a4e;
  --white:#ffffff;
  --muted:#cfcfcf;
  --field:#d9d9d9;
}
*{box-sizing:border-box;margin:0;padding:0}
html,body{width:1200px;height:4938px;overflow:hidden;background:var(--dark);font-family:"Josefin Sans",sans-serif;color:var(--white)}
.page{position:relative;width:1200px;height:4938px}
section,header,footer{position:absolute;left:0;width:1200px}
.abs{position:absolute}
.brand{position:absolute;display:flex;align-items:center;gap:10px}
.brand-box{width:34px;height:34px;border:4px solid var(--white);border-radius:3px}
.brand-name{font-family:"Ubuntu",sans-serif;font-size:40px;font-weight:500;color:var(--white)}
.site-header{top:0;height:107px;background:var(--dark)}
.nav{position:absolute;left:452px;top:44px;display:flex;gap:30px;font-family:"Ubuntu",sans-serif;font-size:15px}
.login{position:absolute;left:981px;top:32px;width:106px;height:46px;border:2px solid var(--red);border-radius:3px;font-family:"Ubuntu",sans-serif;font-weight:700;font-size:14px;display:flex;align-items:center;justify-content:center}
.hero{top:107px;height:602px;background:var(--dark)}
.hero-photo{position:absolute;inset:0;border-bottom-right-radius:150px;background:radial-gradient(ellipse at 50% 70%,#1f4d8c 0%,#1a2438 25%,transparent 55%),linear-gradient(90deg,#3a0f0a 0%,#7a2114 20%,#1a0e10 45%,#1a0e10 55%,#7a2114 80%,#3a0f0a 100%)}
.hero-overlay{position:absolute;inset:0;border-bottom-right-radius:150px;background:rgba(10,10,14,.35)}
.hero-kicker{position:absolute;top:162px;width:100%;text-align:center;font-family:"Ubuntu",sans-serif;font-size:38px;letter-spacing:1px}
.hero-title{position:absolute;top:220px;width:100%;text-align:center;font-family:"Ubuntu",sans-serif;font-weight:700;font-size:62px;letter-spacing:1px}
.hero-points{position:absolute;top:327px;width:100%;display:flex;justify-content:center;gap:48px;font-family:"Ubuntu",sans-serif;font-size:17px}
.hero-points span{display:flex;align-items:center;gap:8px}
.btn-outline{position:absolute;border:2px solid var(--red);font-family:"Ubuntu",sans-serif;font-weight:700;font-size:13px;display:flex;align-items:center;justify-content:center}
.round-arrow{position:absolute;width:42px;height:42px;border:2px solid var(--white);border-radius:50%;display:flex;align-items:center;justify-content:center}
.section-title{position:absolute;width:100%;text-align:center;font-family:"Ubuntu",sans-serif;font-weight:700;font-size:34px;display:flex;justify-content:center;align-items:center;gap:4px}
.title-mark{width:30px;height:30px;border:3px solid #666;border-radius:3px;margin-right:4px}
.hl{color:var(--red)}
.services{top:709px;height:479px}
.service-card{position:absolute;top:167px;width:228px;height:224px;background:var(--card);text-align:center}
.service-card svg.icon{position:absolute;left:74px;top:26px}
.service-card .label{position:absolute;top:134px;width:100%;font-family:"Ubuntu",sans-serif;font-weight:500;font-size:17px;line-height:26px}
.service-card .more{position:absolute;left:102px;top:197px;width:24px;height:24px;border-radius:50%;background:var(--red);display:flex;align-items:center;justify-content:center}
.red-arrow{position:absolute;width:34px;height:34px;border:2px solid var(--red);border-radius:50%;display:flex;align-items:center;justify-content:center}
.about{top:1188px;height:556px;background:linear-gradient(100deg,var(--red-deep),var(--red) 45%,#c93322)}
.about-photo{position:absolute;left:243px;top:192px;width:297px;height:303px;border-bottom-right-radius:60px;background:linear-gradient(160deg,#5b5d63,#1d1f24 60%,#0f1012)}
.about-title{position:absolute;left:672px;top:70px;font-family:"Ubuntu",sans-serif;font-weight:700;font-size:33px;line-height:46px}
.about-text{position:absolute;left:672px;top:182px;width:400px;font-size:12.4px;line-height:23px}
.news{top:1744px;height:662px}
.news-card{position:absolute;top:194px;width:303px}
.news-photo{width:303px;height:217px;box-shadow:6px 6px 0 var(--red);border-bottom-right-radius:10px}
.news-card h3{margin-top:36px;font-family:"Ubuntu",sans-serif;font-weight:500;font-size:19px;line-height:28px}
.btn-red{display:inline-flex;align-items:center;justify-content:center;background:var(--red);font-family:"Ubuntu",sans-serif;font-weight:700;font-size:13px;border-radius:2px}
.news-card .btn-red{margin-top:22px;width:137px;height:42px}
.projects{top:2406px;height:512px;background:linear-gradient(120deg,#263244,#1f2836 50%,#2c3646)}
.project-photo{position:absolute;top:189px;width:228px;height:225px;border-bottom-right-radius:30px;border-top-left-radius:10px}
.blog{top:2918px;height:652px}
.blog-title{position:absolute;left:157px;top:104px;font-family:"Ubuntu",sans-serif;font-weight:700;font-size:34px;display:flex;align-items:center;gap:8px}
.blog-hero-photo{position:absolute;left:122px;top:192px;width:498px;height:180px;background:linear-gradient(120deg,#2a2a30,#6b4b44 40%,#c9c9c9 70%,#8a8f97)}
.blog-card{position:absolute;left:157px;top:370px;width:463px;height:197px;background:var(--white);color:#222;padding:28px 26px}
.meta{font-size:12px;color:#777;display:flex;align-items:center;gap:6px}
.blog-card h4{font-family:"Ubuntu",sans-serif;font-weight:500;font-size:16px;margin-top:14px}
.blog-card p{font-size:12px;color:#666;line-height:20px;margin-top:12px;width:350px}
.read{color:var(--red);font-family:"Ubuntu",sans-serif;font-weight:700;font-size:13px;margin-top:12px;display:block}
.sq-btn{position:absolute;width:32px;height:32px;display:flex;align-items:center;justify-content:center}
.blog-side{position:absolute;left:643px;width:450px;height:177px}
.blog-side .ph{position:absolute;left:0;top:0;width:190px;height:177px}
.blog-side .body{position:absolute;left:217px;top:6px;width:220px}
.blog-side .meta{color:var(--muted)}
.blog-side h4{font-family:"Ubuntu",sans-serif;font-weight:500;font-size:16px;line-height:26px;margin-top:12px}
.blog-side p{font-size:11px;line-height:19px;margin-top:8px}
.partners{top:3570px;height:475px;background:linear-gradient(100deg,var(--red-deep),var(--red) 50%,var(--red-deep))}
.partner{position:absolute;top:218px;width:166px;height:166px;border-radius:50%;background:var(--white);display:flex;align-items:center;justify-content:center;font-family:"Ubuntu",sans-serif;font-weight:700;font-size:20px;color:#333}
.chev{position:absolute;font-family:"Ubuntu",sans-serif;font-size:24px}
.contact{top:4045px;height:595px}
.field{position:absolute;height:44px;border:1px solid #bdbdbd;font-size:15px;color:var(--field);padding:14px 22px}
.submit{position:absolute;left:532px;top:490px;width:136px;height:39px;background:var(--red);border-radius:3px;font-family:"Ubuntu",sans-serif;font-weight:700;font-size:14px;display:flex;align-items:center;justify-content:center}
.site-footer{top:4640px;height:298px;background:var(--darker);border-top-left-radius:150px}
.info{position:absolute;display:flex;gap:16px;align-items:flex-start}
.info .ring{width:58px;height:58px;border:2px solid var(--red);border-radius:50%;display:flex;align-items:center;justify-content:center;flex:none}
.info strong{display:block;font-family:"Ubuntu",sans-serif;font-size:14px;margin-bottom:8px}
.info span{font-size:11.5px;line-height:20px}
.copyright{position:absolute;left:113px;top:256px;font-size:13px}
.social{position:absolute;top:240px;width:36px;height:36px;border:2px solid var(--white);border-radius:50%}
</style>
</head>
<body>
<div class="page">

<header class="site-header">
  <div class="brand" style="left:113px;top:28px"><span class="brand-box"></span><span class="brand-name">Lumora</span></div>
  <nav class="nav"><span>Home</span><span>About</span><span>Our Services</span><span>Our Projects</span><span>Contact</span></nav>
  <div class="login">LOG IN</div>
</header>

<section class="hero">
  <div class="hero-photo" role="img" aria-label="Server room corridor lit in red with blue floor glow"></div>
  <div class="hero-overlay"></div>
  <div class="hero-kicker">WECOME TO</div>
  <div class="hero-title">LUMORA SYSTEMS</div>
  <div class="hero-points">
    <span><svg width="16" height="16" viewBox="0 0 16 16"><circle cx="8" cy="8" r="7" fill="none" stroke="#d8392a" stroke-width="1.5"/><path d="M4.5 8l2.5 2.5 4.5-5" fill="none" stroke="#d8392a" stroke-width="1.5"/></svg>IT INFRASTRUCTURE</span>
    <span><svg width="16" height="16" viewBox="0 0 16 16"><circle cx="8" cy="8" r="7" fill="none" stroke="#d8392a" stroke-width="1.5"/><path d="M4.5 8l2.5 2.5 4.5-5" fill="none" stroke="#d8392a" stroke-width="1.5"/></svg>SMART CABINET</span>
    <span><svg width="16" height="16" viewBox="0 0 16 16"><circle cx="8" cy="8" r="7" fill="none" stroke="#d8392a" stroke-width="1.5"/><path d="M4.5 8l2.5 2.5 4.5-5" fill="none" stroke="#d8392a" stroke-width="1.5"/></svg>MICRO DATA CENTER</span>
  </div>
  <div class="btn-outline" style="left:533px;top:387px;width:133px;height:42px;background:rgba(20,20,24,.6)">GET STARTED</div>
  <div class="round-arrow" style="left:51px;top:257px"><svg width="14" height="14" viewBox="0 0 14 14"><path d="M9 2L4 7l5 5" fill="none" stroke="#fff" stroke-width="2"/></svg></div>
  <div class="round-arrow" style="left:1107px;top:257px"><svg width="14" height="14" viewBox="0 0 14 14"><path d="M5 2l5 5-5 5" fill="none" stroke="#fff" stroke-width="2"/></svg></div>
</section>

<section class="services">
  <h2 class="section-title" style="top:76px"><span class="title-mark"></span>OUR <span class="hl">SERVICES</span></h2>
  <div class="red-arrow" style="left:61px;top:262px"><svg width="12" height="12" viewBox="0 0 12 12"><path d="M8 1L3 6l5 5" fill="none" stroke="#fff" stroke-width="2"/></svg></div>
  <div class="red-arrow" style="left:1105px;top:262px"><svg width="12" height="12" viewBox="0 0 12 12"><path d="M4 1l5 5-5 5" fill="none" stroke="#d8392a" stroke-width="2"/></svg></div>

  <div class="service-card" style="left:111px">
    <svg class="icon" width="80" height="80" viewBox="0 0 80 80" fill="none" stroke="#d8392a" stroke-width="2.5"><rect x="6" y="22" width="22" height="44"/><rect x="29" y="6" width="22" height="60"/><rect x="52" y="22" width="22" height="44"/><path d="M10 32h14M10 42h14M33 16h14M33 28h14M56 32h14M56 42h14"/><ellipse cx="40" cy="66" rx="22" ry="8"/></svg>
    <div class="label">Data center design<br>and build</div>
    <div class="more"><svg width="12" height="12" viewBox="0 0 12 12"><path d="M2 4l4 4 4-4" fill="none" stroke="#fff" stroke-width="2"/></svg></div>
  </div>
  <div class="service-card" style="left:361px">
    <svg class="icon" width="80" height="80" viewBox="0 0 80 80" fill="none" stroke="#d8392a" stroke-width="2.5"><rect x="28" y="34" width="18" height="40"/><path d="M32 44h10M32 52h10M32 60h10M37 34V20M37 20l-10-14M37 20l8-10M45 14l12 4M55 18l4 14"/></svg>
    <div class="label">StructureD cabling and<br>fiber backbone</div>
    <div class="more"><svg width="12" height="12" viewBox="0 0 12 12"><path d="M2 4l4 4 4-4" fill="none" stroke="#fff" stroke-width="2"/></svg></div>
  </div>
  <div class="service-card" style="left:611px">
    <svg class="icon" width="80" height="80" viewBox="0 0 80 80" fill="none" stroke="#d8392a" stroke-width="2.5"><path d="M24 6h32v68H24zM32 6v12M40 6v12M48 6v12"/><rect x="30" y="40" width="20" height="24" rx="3"/></svg>
    <div class="label">Micro-Data Center</div>
    <div class="more"><svg width="12" height="12" viewBox="0 0 12 12"><path d="M2 4l4 4 4-4" fill="none" stroke="#fff" stroke-width="2"/></svg></div>
  </div>
  <div class="service-card" style="left:861px">
    <svg class="icon" width="80" height="80" viewBox="0 0 80 80" fill="none" stroke="#d8392a" stroke-width="2.5"><rect x="14" y="8" width="52" height="30"/><path d="M20 30l10-10 8 6 12-12 8 6M22 46h36M28 46l-8 26M52 46l8 26M34 58h12"/></svg>
    <div class="label">Audiovisual and<br>Conference Room</div>
    <div class="more"><svg width="12" height="12" viewBox="0 0 12 12"><path d="M2 4l4 4 4-4" fill="none" stroke="#fff" stroke-width="2"/></svg></div>
  </div>
</section>

<section class="about">
  <div class="about-photo" role="img" aria-label="Row of black server racks in a data center aisle"></div>
  <h2 class="about-title"><span style="display:inline-block;width:30px;height:30px;border:3px solid rgba(255,255,255,.45);border-radius:3px;margin-right:6px;vertical-align:-4px"></span>ABOUT LUMORA<br>SYSTEMS</h2>
  <p class="about-text">Lumora Systems is well experienced in delivering the best in Data Center Infrastructure, Network Infrastructure, Structured Cabling, Telephony, Access Control, Video Surveillance, Audio-visual &amp; Conferencing, Relocation &amp; Migration and Maintenance solutions. Our dedication, focus, and expertise wins much recognition of many IT professionals in all industries in the region. In Lumora Systems's Belief, the major reason that we gain a lot of true long-lasting business relationship with our clients was that we offer them the attention, consideration, passion, and professionalism that they deserved.</p>
  <div class="btn-outline" style="left:672px;top:444px;width:133px;height:45px;border-color:#fff">LEARN MORE</div>
</section>

<section class="news">
  <h2 class="section-title" style="top:104px"><span class="title-mark"></span>NEWS AND <span class="hl">&nbsp;EVENTS</span></h2>
  <article class="news-card" style="left:106px">
    <div class="news-photo" role="img" aria-label="Blue lit data center corridor" style="background:linear-gradient(180deg,#0b2a66,#1c5fc2 50%,#0a1838)"></div>
    <h3>Lorem ipsum dolor sit amet,<br>consectetur...</h3>
    <span class="btn-red">LEARN MORE</span>
  </article>
  <article class="news-card" style="left:444px">
    <div class="news-photo" role="img" aria-label="Modern server hall with reception desk" style="background:linear-gradient(180deg,#3a3a3e,#8a6a4a 50%,#2a2a2e)"></div>
    <h3>Lorem ipsum dolor sit amet,<br>consectetur...</h3>
    <span class="btn-red">LEARN MORE</span>
  </article>
  <article class="news-card" style="left:782px">
    <div class="news-photo" role="img" aria-label="Network operations center with wall screens" style="background:linear-gradient(180deg,#1a3b66,#2d5d8e 45%,#1b2230)"></div>
    <h3>Lorem ipsum dolor sit amet,<br>consectetur...</h3>
    <span class="btn-red">LEARN MORE</span>
  </article>
</section>

<section class="projects" role="img" aria-label="Dim server room background">
  <h2 class="section-title" style="top:80px"><span class="title-mark"></span>OUR P<span class="hl">ROJECT</span></h2>
  <div class="project-photo" role="img" aria-label="Black smart cabinet" style="left:111px;background:linear-gradient(90deg,#111,#333 50%,#1a1a1a)"></div>
  <div class="project-photo" role="img" aria-label="Patch panel with blue cables" style="left:361px;border:3px solid var(--red);background:linear-gradient(180deg,#1d4a86,#3a7ad0 50%,#1b3660)"></div>
  <div class="project-photo" role="img" aria-label="Cabinet control panel" style="left:611px;background:linear-gradient(90deg,#555,#888 50%,#3a3a3a)"></div>
  <div class="project-photo" role="img" aria-label="Rack with bundled blue cabling" style="left:861px;background:linear-gradient(90deg,#1a1a1a,#3d7cc9 40%,#222)"></div>
</section>

<section class="blog">
  <h2 class="blog-title"><span class="title-mark"></span>LATEST <span class="hl">BLOG</span></h2>
  <div class="blog-hero-photo" role="img" aria-label="Network cabinet wiring and breakers"></div>
  <article class="blog-card">
    <div class="meta"><svg width="12" height="12" viewBox="0 0 12 12"><circle cx="6" cy="6" r="5" fill="none" stroke="#d8392a" stroke-width="1.5"/><path d="M6 3v3h2" stroke="#d8392a" stroke-width="1.5" fill="none"/></svg>December 19,2023</div>
    <h4>Sed ut perspiciatis unde omnis iste</h4>
    <p>Lorem ipsum dolor sit amet, consectetur adipiscing elit, sed do eiusmod tempor incididunt ut labore et dolore</p>
    <span class="read">READ MORE →</span>
    <div class="sq-btn" style="left:406px;top:70px;background:var(--red)"><svg width="12" height="12" viewBox="0 0 12 12"><path d="M4 1l5 5-5 5" fill="none" stroke="#fff" stroke-width="2"/></svg></div>
    <div class="sq-btn" style="left:406px;top:110px;background:#ddd"><svg width="12" height="12" viewBox="0 0 12 12"><path d="M8 1L3 6l5 5" fill="none" stroke="#888" stroke-width="2"/></svg></div>
  </article>
  <article class="blog-side" style="top:188px">
    <div class="ph" role="img" aria-label="Server room with cabinets" style="background:linear-gradient(90deg,#777,#2a2a2a 60%,#555)"></div>
    <div class="body">
      <div class="meta"><svg width="12" height="12" viewBox="0 0 12 12"><circle cx="6" cy="6" r="5" fill="none" stroke="#d8392a" stroke-width="1.5"/><path d="M6 3v3h2" stroke="#d8392a" stroke-width="1.5" fill="none"/></svg>December 19,2023</div>
      <h4>Sed ut perspiciatis unde<br>omnis iste</h4>
      <p>Lorem ipsum dolor sit amet, consectetur adipiscing elit, sed do eiusmod tempor incididunt</p>
      <span class="read">READ MORE →</span>
    </div>
  </article>
  <article class="blog-side" style="top:392px">
    <div class="ph" role="img" aria-label="Presentation about sustainability approach" style="background:linear-gradient(120deg,#1b1d2a,#3b3550 50%,#6b3a8a)"></div>
    <div class="body">
      <div class="meta"><svg width="12" height="12" viewBox="0 0 12 12"><circle cx="6" cy="6" r="5" fill="none" stroke="#d8392a" stroke-width="1.5"/><path d="M6 3v3h2" stroke="#d8392a" stroke-width="1.5" fill="none"/></svg>December 19,2023</div>
      <h4>Sed ut perspiciatis unde<br>omnis iste</h4>
      <p>Lorem ipsum dolor sit amet, consectetur adipiscing elit, sed do eiusmod tempor incididunt</p>
      <span class="read">READ MORE →</span>
    </div>
  </article>
</section>

<section class="partners">
  <h2 class="section-title" style="top:108px"><span class="title-mark" style="border-color:rgba(255,255,255,.45)"></span>PARTNERS AND BRANDS</h2>
  <span class="chev" style="left:64px;top:285px">‹</span>
  <span class="chev" style="left:1120px;top:285px">›</span>
  <div class="partner" style="left:142px">Coldmark</div>
  <div class="partner" style="left:343px">Brandhal</div>
  <div class="partner" style="left:545px">Zentrio</div>
  <div class="partner" style="left:747px">Vaultra</div>
  <div class="partner" style="left:948px">Parlink</div>
</section>

<section class="contact">
  <h2 class="section-title" style="top:103px"><span class="title-mark"></span>CONTACT <span class="hl">&nbsp;US</span></h2>
  <div class="field" style="left:297px;top:194px;width:296px">Name</div>
  <div class="field" style="left:605px;top:194px;width:297px">Email</div>
  <div class="field" style="left:297px;top:262px;width:296px">Name</div>
  <div class="field" style="left:605px;top:262px;width:297px">Email</div>
  <div class="field" style="left:297px;top:331px;width:605px;height:104px">Message</div>
  <div class="submit">SUBMIT NOW</div>
</section>

<footer class="site-footer">
  <div class="brand" style="left:113px;top:102px"><span class="brand-box"></span><span class="brand-name">Lumora</span></div>
  <div class="info" style="left:411px;top:82px">
    <div class="ring"><svg width="20" height="20" viewBox="0 0 20 20"><path d="M10 1a6 6 0 0 0-6 6c0 5 6 12 6 12s6-7 6-12a6 6 0 0 0-6-6z" fill="#fff"/><circle cx="10" cy="7" r="2.2" fill="#1c1c1c"/></svg></div>
    <div><strong>Address</strong><span>Rm 1208, 12/F, Harbourline Plaza,<br>18 Kin Fat Street,</span></div>
  </div>
  <div class="info" style="left:695px;top:98px">
    <div class="ring"><svg width="18" height="18" viewBox="0 0 24 24"><path d="M6.6 10.8a15 15 0 0 0 6.6 6.6l2.2-2.2a1 1 0 0 1 1-.25 11.4 11.4 0 0 0 3.6.57 1 1 0 0 1 1 1V20a1 1 0 0 1-1 1A17 17 0 0 1 3 4a1 1 0 0 1 1-1h3.5a1 1 0 0 1 1 1c0 1.25.2 2.45.57 3.57a1 1 0 0 1-.25 1z" fill="#fff"/></svg></div>
    <div><strong>Phone</strong><span>+852 2684 1930</span></div>
  </div>
  <div class="info" style="left:881px;top:98px">
    <div class="ring"><svg width="18" height="14" viewBox="0 0 18 14"><rect x="0" y="0" width="18" height="14" rx="1.5" fill="#fff"/><path d="M1 1l8 6 8-6" fill="none" stroke="#1c1c1c" stroke-width="1.6"/></svg></div>
    <div><strong>Email</strong><span>marketing@lumorasys.com.hk</span></div>
  </div>
  <div class="copyright">©Copyrights 2023 Lumorasys &nbsp;| &nbsp; All Rights Reserved</div>
  <div class="social" style="left:997px"></div>
  <div class="social" style="left:1045px"></div>
</footer>

</div>
</body>
</html>
```